Mental Health care Company in Washington DC

We are a new mental health care services provider in Washington DC. Please look at these sites.
https://brightwaterfamilysupport.com
https://www.quietharborinc.com
https://willowgate-dc.org/
https://www.tidepathdc.com
https://www.thelanternofdc.com

```html
<!DOCTYPE html>
<html lang="en">
<head>
<meta charset="utf-8">
<title>Vela Health Services</title>
<link href="https://fonts.googleapis.com/css2?family=Poppins:wght@400;500;600;700&display=swap" rel="stylesheet">
<style>
:root{
  --navy:#0f1f44;
  --orange:#f47b20;
  --teal:#3bb8c4;
  --mint:#93d5d6;
  --mist:#f4f5f9;
  --ink:#2b2f3a;
  --line:#e3e6ee;
  --white:#ffffff;
}
*{box-sizing:border-box;margin:0;padding:0}
html,body{width:1200px;height:4484px;overflow:hidden}
body{font-family:'Poppins',sans-serif;color:var(--ink);background:var(--white);position:relative}
.abs{position:absolute}
.topbar{left:0;top:0;width:1200px;height:28px;background:var(--navy);color:#fff;font-size:10px;text-align:center;line-height:28px;letter-spacing:.3px}
.nav{left:0;top:28px;width:1200px;height:80px;background:#fff}
.brand{position:absolute;display:flex;align-items:center;gap:10px;white-space:nowrap;font-weight:600;line-height:1}
.brand .dot{display:block;width:12px;height:12px;border-radius:50%;background:var(--orange);flex:none}
.menu{position:absolute;left:413px;top:32px;display:flex;gap:28px;font-size:13px;color:var(--navy)}
.btn{position:absolute;border-radius:20px;font-weight:500;text-align:center;color:#fff;background:var(--orange)}
.hero{left:0;top:108px;width:1200px;height:660px;overflow:hidden}
.hero-photo{position:absolute;inset:0;background:linear-gradient(90deg,#1d3a58 0%,#3d5d74 40%,#9aa7ac 70%,#d8d3cc 100%)}
.hero h1{position:absolute;left:141px;top:118px;font-size:48px;line-height:56px;color:#fff;font-weight:700}
.hero h1 span{color:var(--teal)}
.hero p{position:absolute;left:141px;top:252px;font-size:14.5px;line-height:26px;color:#fff}
.eyebrow{font-size:14px;color:var(--teal);font-weight:500;letter-spacing:.3px}
.h2{font-size:30px;font-weight:600;color:var(--navy);line-height:36px}
.center{left:0;width:1200px;text-align:center}
.divider{position:absolute;left:560px;width:80px;height:12px}
.divider::before{content:"";position:absolute;left:0;right:0;top:6px;height:1px;background:#cfd3dc}
.divider::after{content:"";position:absolute;left:35px;top:1px;width:10px;height:10px;border-radius:50%;background:var(--orange);box-shadow:0 0 0 3px #fff}
.band{left:0;width:1200px;background:var(--mist)}
.svc{position:absolute;top:1434px;width:294px;height:230px;background:#fff;border-radius:12px;overflow:hidden;box-shadow:0 6px 18px rgba(15,31,68,.08)}
.svc .ph{height:174px}
.svc .lbl{position:absolute;left:24px;top:196px;font-size:15px;font-weight:500;color:var(--navy)}
.svc svg{position:absolute;right:28px;top:194px}
.svc.active{background:var(--orange)}
.svc.active .lbl{color:#fff}
.dots{position:absolute;left:554px;display:flex;gap:9px}
.dots i{display:block;width:16px;height:4px;border-radius:2px;background:#cfd3dc}
.dots i:first-child{background:var(--orange)}
.tcard{position:absolute;top:2007px;width:361px;height:258px;background:#fff;border-radius:10px;box-shadow:0 4px 20px rgba(15,31,68,.08)}
.tcard .in{position:absolute;left:12px;top:12px;right:12px;bottom:12px;border:1px solid var(--line);border-radius:8px;padding:22px 24px}
.tcard h4{font-size:15px;font-weight:500;color:var(--navy)}
.tcard .stars{color:var(--orange);font-size:14px;letter-spacing:2px}
.tcard .g{position:absolute;right:24px;top:26px;width:28px;height:28px;border-radius:50%;background:#e9ecf2}
.tcard hr{border:0;border-top:1px solid var(--line);margin:14px 0 18px}
.tcard p{font-size:13px;line-height:24px;color:#444}
.tcard .q{position:absolute;right:18px;bottom:-46px;font-size:110px;line-height:1;color:var(--teal);font-weight:700}
.arrowbtn{position:absolute;top:1913px;width:39px;height:38px;display:flex;align-items:center;justify-content:center}
.member{position:absolute;top:2583px;width:288px;height:340px;border-radius:10px}
.mcard{position:absolute;top:2881px;width:232px;height:129px;background:#fff;border-radius:10px;text-align:center;box-shadow:0 6px 18px rgba(15,31,68,.07)}
.mcard h5{margin-top:26px;font-size:17px;font-weight:500;color:var(--navy)}
.mcard small{display:block;font-size:11.5px;color:#666;margin-top:2px}
.mcard .soc{display:flex;justify-content:center;gap:14px;margin-top:14px}
.mcard .soc i{display:block;width:11px;height:11px;border-radius:50%;background:var(--orange)}
.faq{left:141px;top:3343px;width:916px;height:423px;background:#fff;border:1px solid var(--line);z-index:2}
.row{position:absolute;left:0;width:914px;border-bottom:1px solid var(--line);padding-left:52px;font-size:15px;font-weight:500;color:var(--navy)}
.row .pm{position:absolute;right:18px;width:28px;height:28px;border-radius:50%;background:var(--navy);color:#fff;text-align:center;line-height:27px;font-size:18px}
.row.open{background:var(--mist);border-left:3px solid var(--orange)}
.row.open .pm{background:var(--orange)}
.row.open p{font-size:13px;font-weight:400;color:#444;line-height:24px;margin-top:14px;width:760px}
.footer{left:0;top:3600px;width:1200px;height:884px}
.fcol{position:absolute;top:4125px;color:#fff}
.fcol h6{font-size:17px;font-weight:500;margin-bottom:26px}
.fcol h6::after{content:"";display:block;width:36px;height:2px;background:var(--teal);margin-top:4px}
.fcol a{display:block;font-size:12.5px;color:#fff;text-decoration:none;margin-bottom:14px}
.ci{position:absolute;left:543px;display:flex;align-items:center;gap:14px;font-size:12.5px;line-height:21px;color:#fff}
.ci .ic{width:32px;height:32px;border-radius:50%;background:#fff;display:flex;align-items:center;justify-content:center;flex:none}
</style>
</head>
<body>

<div class="abs topbar">WELCOME TO VELA HEALTH – EMPOWERING MENTAL WELLNESS IN DC</div>

<header class="abs nav">
  <div class="brand" style="left:141px;top:29px;font-size:21px;color:var(--navy)"><span class="dot"></span>Vela Health Services</div>
  <nav class="menu"><span>Home</span><span>About Us ▾</span><span>Services ▾</span><span>Blog</span><span>FAQs</span><span>Contact</span></nav>
  <div class="btn" style="left:865px;top:22px;width:194px;height:36px;line-height:36px;font-size:13px">Make an Appointment</div>
</header>

<section class="abs hero">
  <div class="hero-photo" role="img" aria-label="Smiling young caregiver with a hand on the shoulder of an older man beside a potted plant"></div>
  <h1>Empowering Minds<span>.</span><br>Restoring Lives<span>.</span></h1>
  <p>Compassionate, Client-Centered Mental Health Services<br>Tailored For Washington DC's Diverse Communities.</p>
  <div class="btn" style="left:141px;top:340px;width:139px;height:33px;line-height:33px;font-size:13px;background:var(--mint);color:var(--navy)">Get Started</div>
  <svg class="abs" style="left:0;top:0" width="1200" height="660" viewBox="0 0 1200 660">
    <path d="M0 660 L0 650 C180 520 420 560 640 540 C900 510 1080 420 1200 250 L1200 660 Z" fill="var(--orange)"/>
    <path d="M0 660 L0 690 C180 560 420 590 640 572 C900 545 1090 450 1200 290 L1200 660 Z" fill="#fff"/>
  </svg>
  <div class="abs" style="left:831px;top:439px;width:114px;height:114px;border-radius:50%;background:#fff;border:5px solid var(--orange)"></div>
</section>

<section>
  <div class="abs" style="left:126px;top:723px;width:436px;height:436px;border-radius:50%;background:var(--orange)"></div>
  <div class="abs" role="img" aria-label="Doctor in white coat shaking hands with a patient in a clinic" style="left:136px;top:723px;width:430px;height:430px;border-radius:50%;background:linear-gradient(135deg,#c9d3dc,#6f8aa3 60%,#34506c)"></div>
  <div class="abs eyebrow" style="left:629px;top:748px">WHO WE ARE <span style="display:inline-block;width:70px;height:1px;background:#cfd3dc;vertical-align:middle;margin-left:8px"></span></div>
  <div class="abs h2" style="left:629px;top:782px">A Trusted Mental Health<br>Partner In DC</div>
  <p class="abs" style="left:629px;top:868px;width:430px;font-size:12.5px;line-height:22.5px;color:#333">Lorem Ipsum is simply dummy text of the printing and typesetting industry. Lorem Ipsum has been the industry's standard dummy text ever since the 1500s, when an unknown printer took a galley of type and scrambled it to make a type specimen book. It has survived not only five centuries, but also the leap into electronic typesetting, remaining essentially unchanged. It was popularised in the 1960s with the release of Letraset sheets containing Lorem Ipsum passages, and more recently with desktop publishing software like Aldus PageMaker including versions of Lorem Ipsum</p>
  <div class="btn" style="left:629px;top:1101px;width:193px;height:33px;line-height:33px;font-size:12px">Learn More About Us</div>
</section>

<section class="abs band" style="top:1228px;height:575px"></section>
<div class="abs center eyebrow" style="top:1316px">OUR CORE SERVICES</div>
<div class="divider" style="top:1342px"></div>
<div class="abs center h2" style="top:1360px">Transformative Services For Real Results</div>
<div class="svc" style="left:139px"><div class="ph" role="img" aria-label="Woman talking with a therapist on a sofa" style="background:linear-gradient(135deg,#e8e2dc,#c9a99a)"></div><span class="lbl">Individual Therapy</span><svg width="20" height="20" viewBox="0 0 20 20"><path d="M4 16 L16 4 M7 4 H16 V13" stroke="var(--navy)" stroke-width="1.6" fill="none"/></svg></div>
<div class="svc active" style="left:453px"><div class="ph" role="img" aria-label="Group of medical staff standing together" style="background:linear-gradient(135deg,#dfe4ea,#8a9bb0)"></div><span class="lbl">Support Groups</span><svg width="24" height="20" viewBox="0 0 24 20"><path d="M2 10 H21 M14 3 L21 10 L14 17" stroke="#fff" stroke-width="1.6" fill="none"/></svg></div>
<div class="svc" style="left:768px"><div class="ph" role="img" aria-label="Nurse comforting an older woman at a desk" style="background:linear-gradient(135deg,#6a8aa6,#c3cfdb)"></div><span class="lbl">Counseling</span><svg width="20" height="20" viewBox="0 0 20 20"><path d="M4 16 L16 4 M7 4 H16 V13" stroke="var(--navy)" stroke-width="1.6" fill="none"/></svg></div>
<div class="dots" style="top:1712px"><i></i><i></i><i></i><i></i></div>

<section>
  <div class="abs eyebrow" style="left:141px;top:1889px">CLIENT TESTIMONIALS <span style="display:inline-block;width:70px;height:1px;background:#cfd3dc;vertical-align:middle;margin-left:8px"></span></div>
  <div class="abs h2" style="left:141px;top:1923px">A Trusted Mental Health Partner In DC</div>
  <div class="arrowbtn" style="left:970px;background:var(--orange)"><svg width="12" height="14" viewBox="0 0 12 14"><path d="M8 2 L3 7 L8 12" stroke="#fff" stroke-width="2" fill="none"/></svg></div>
  <div class="arrowbtn" style="left:1023px;background:var(--navy)"><svg width="12" height="14" viewBox="0 0 12 14"><path d="M4 2 L9 7 L4 12" stroke="#fff" stroke-width="2" fill="none"/></svg></div>
  <div class="tcard" style="left:139px"><div class="in"><h4>Marla Quinn</h4><div class="stars">★★★★★</div><span class="g"></span><hr><p>Lorem Ipsum is simply dummy text of the printing and typesetting industry. Lorem Ipsum has been the industry's standard dummy text ever since the 1500s.</p></div><div class="q">”</div></div>
  <div class="tcard" style="left:530px"><div class="in"><h4>Dexter Hollins</h4><div class="stars">★★★★★</div><span class="g"></span><hr><p>Lorem Ipsum is simply dummy text of the printing and typesetting industry. Lorem Ipsum has been the industry's standard dummy text ever since the 1500s.</p></div><div class="q">”</div></div>
  <div class="tcard" style="left:921px"><div class="in" style="right:-12px"><h4>J. Ferris</h4><div class="stars">★★★★★</div><hr><p style="white-space:nowrap">Lorem Ipsum is simply dummy text of<br>printing and typesetting industry. Lo<br>Ipsum has been the industry's stand<br>dummy text ever since the 1500s.</p></div></div>
</section>

<section class="abs band" style="top:2374px;height:765px"></section>
<div class="abs center eyebrow" style="top:2462px">MEET OUR TEAM</div>
<div class="divider" style="top:2488px"></div>
<div class="abs center h2" style="top:2508px">Meet The Minds Behind The Mission</div>
<div class="member" style="left:141px;background:linear-gradient(180deg,#e6e6e6,#cfd2d6)" role="img" aria-label="Male doctor in white coat with stethoscope, arms crossed"></div>
<div class="member" style="left:458px;background:linear-gradient(135deg,#d9d4cc,#a59a8a)" role="img" aria-label="Female doctor in white coat standing in an office"></div>
<div class="member" style="left:775px;background:linear-gradient(180deg,#eef0f2,#d2d7dc)" role="img" aria-label="Female doctor in blue scrubs and white coat, arms crossed"></div>
<div class="mcard" style="left:169px"><h5>Owen Pratt</h5><small>Anxiety Specialist</small><div class="soc"><i></i><i></i><i></i><i></i></div></div>
<div class="mcard" style="left:486px"><h5>Lena Vasquez</h5><small>Trauma Expert</small><div class="soc"><i></i><i></i><i></i><i></i></div></div>
<div class="mcard" style="left:803px"><h5>Nora Bellamy</h5><small>Group Therapy Lead</small><div class="soc"><i></i><i></i><i></i><i></i></div></div>
<div class="dots" style="top:3046px"><i></i><i></i><i></i><i></i></div>

<div class="abs center eyebrow" style="top:3227px">FAQs</div>
<div class="divider" style="top:3253px"></div>
<div class="abs center h2" style="top:3273px">Frequently Asked Questions</div>

<svg class="abs footer" viewBox="0 0 1200 884" width="1200" height="884">
  <path d="M0 60 C120 220 300 300 560 330 C820 360 1000 320 1200 420 L1200 884 L0 884 Z" fill="var(--navy)"/>
</svg>

<div class="abs faq">
  <div class="row" style="top:0;height:70px;line-height:70px">Who Is Your Primary Target Audience?<span class="pm" style="top:20px">+</span></div>
  <div class="row" style="top:70px;height:67px;line-height:67px">What Are The Top 3 Actions You Want Visitors To Take On The Website?<span class="pm" style="top:19px">+</span></div>
  <div class="row open" style="top:137px;height:149px;padding-top:30px;padding-left:49px">Do You Have Existing Branding Elements To Incorporate, Or Should The Design Start Fresh?<span class="pm" style="top:26px">−</span><p>Lorem Ipsum is simply dummy text of the printing and typesetting industry. Lorem Ipsum has been the industry's standard dummy text ever since the 1500s.</p></div>
  <div class="row" style="top:286px;height:68px;line-height:68px">Are There Any Specific Services Or Features That Must Be Highlighted Or Integrated?<span class="pm" style="top:20px">+</span></div>
  <div class="row" style="top:354px;height:68px;line-height:68px;border-bottom:0">What Is Your Preferred Timeline And Budget For Launching The Website?<span class="pm" style="top:20px">+</span></div>
</div>

<footer>
  <div class="brand" style="left:0;width:1200px;justify-content:center;top:4036px;font-size:28px;color:#fff"><span class="dot" style="width:14px;height:14px"></span>Vela Health Services</div>
  <div class="fcol" style="left:141px"><h6>Quick Links</h6><a>Home</a><a>About Us</a><a>Services</a><a>Blog</a><a>FAQs</a></div>
  <div class="fcol" style="left:338px"><h6>Useful Links</h6><a>Contact Us</a><a>Privacy Policy</a><a>Terms &amp; Conditions</a></div>
  <div class="fcol" style="left:543px"><h6>Contact Us</h6></div>
  <div class="ci" style="top:4180px"><span class="ic"><svg width="14" height="16" viewBox="0 0 14 16"><path d="M7 15 C3 10 1.5 7.5 1.5 5.5 A5.5 5.5 0 0 1 12.5 5.5 C12.5 7.5 11 10 7 15 Z" fill="var(--orange)"/><circle cx="7" cy="5.5" r="2" fill="#fff"/></svg></span><span>123, Lorem Ipsum is simply<br>dummy text of the printing</span></div>
  <div class="ci" style="top:4240px"><span class="ic"><svg width="14" height="14" viewBox="0 0 14 14"><path d="M3 1 L5.5 1 L6.5 4 L5 5.5 C5.8 7.2 6.8 8.2 8.5 9 L10 7.5 L13 8.5 L13 11 C13 12 12 13 11 13 C6 13 1 8 1 3 C1 2 2 1 3 1 Z" fill="var(--orange)"/></svg></span><span>Phone: (123)-456-7890</span></div>
  <div class="ci" style="top:4297px"><span class="ic"><svg width="16" height="12" viewBox="0 0 16 12"><rect x="1" y="1" width="14" height="10" rx="1.5" fill="var(--orange)"/><path d="M1.5 1.5 L8 7 L14.5 1.5" stroke="#fff" stroke-width="1.2" fill="none"/></svg></span><span>info@velamentalhealth.com</span></div>
  <div class="fcol" style="left:855px"><h6>Newsletter</h6><p style="font-size:12px;line-height:19px;margin-top:-10px;width:210px">Join our subscribers list to get the latest news &amp; special offers.</p></div>
  <div class="abs" style="left:855px;top:4238px;width:197px;height:38px;border-radius:19px;background:#fff;font-size:11px;color:#999;line-height:38px;padding-left:20px">Enter your email<svg style="position:absolute;right:16px;top:13px" width="16" height="12" viewBox="0 0 16 12"><rect x="1" y="1" width="14" height="10" rx="1.5" stroke="#999" fill="none"/><path d="M1.5 1.5 L8 7 L14.5 1.5" stroke="#999" fill="none"/></svg></div>
  <div class="btn" style="left:855px;top:4295px;width:197px;height:37px;line-height:37px;font-size:12.5px;font-weight:600">SUBSCRIBE NOW</div>
  <div class="abs" style="left:70px;top:4398px;width:1059px;height:1px;background:rgba(255,255,255,.25)"></div>
  <div class="abs center" style="top:4420px;font-size:11.5px;color:#fff">Copyright © 2025 Vela Mental Health | All Rights Reserved.</div>
</footer>

</body>
</html>
```